Tidewell Horizon Magazine need Logo desing and front page for 1 edittion

This is a new magazine that will be circulating in Panama. the magazine will run non for profit,will be mostly informative and few advertizers to cover printing costs.
the magaine will oncce every 2 or 3 month. we need to present it to the editors who will be aproving or diss aproving the project.

we need a Logo desing for the name of the magazine "Tidewell Horizon" and the "front cover desing for the first edition" it will be good if the designer can incude the designed format for the iner magazine, for us just to add in the artucles and the spaces for advertizing.

the magazine content will be articles by govenment energy sectors, gloval warming articles, articles in renewvable enery, university profesor talking or promoting new ideas or university advances, orientations, special edition on book or international articles about the subject on saving enerty, different sectors, world innovations in renewbable energy, and the companies who will advertize will be comapnies selling VORN products, companies offfering product and services on renewvable energy, Led product and systems companies etc...

Printing

```html
<!DOCTYPE html>
<html lang="en">
<head>
<meta charset="utf-8">
<title>Tidewell Horizon — Spread 12–13</title>
<link rel="stylesheet" href="https://fonts.googleapis.com/css2?family=Playfair+Display:wght@700;900&family=Jost:ital,wght@0,300;0,400;0,500;1,400&display=swap">
<style>
  :root {
    --sun-yellow: #f7c800;
    --leaf-green: #22a34a;
    --box-green: #2eaa4c;
    --tag-red: #d42a2a;
    --ink: #1d2230;
    --ink-soft: #2b2b2b;
    --paper: #ffffff;
    --sky-deep: #2456b4;
    --sky-mid: #6f9fd8;
    --sky-light: #b7d0ec;
    --panel-blue: #24407f;
    --bulb-light: #eef0ee;
    --stem-green: #3aa43a;
  }
  * { box-sizing: border-box; margin: 0; padding: 0; }
  html, body { width: 1200px; height: 776px; overflow: hidden; background: var(--paper); }
  .spread { position: relative; width: 1200px; height: 776px; overflow: hidden; }
  .page { position: absolute; top: 0; width: 600px; height: 776px; overflow: hidden; }
  .page--left { left: 0; }
  .page--right { left: 600px; background: var(--paper); }

  .photo-solar {
    position: absolute; inset: 0;
    background: linear-gradient(180deg, var(--sky-deep) 0%, var(--sky-mid) 28%, var(--sky-light) 50%, var(--sky-mid) 66%, var(--panel-blue) 100%);
  }
  .photo-bulb {
    position: absolute; left: 392px; top: 336px; width: 208px; height: 440px;
    background: linear-gradient(180deg, var(--bulb-light) 0%, #dfe6de 45%, #8fcf73 75%, var(--stem-green) 100%);
  }

  .section-tag {
    position: absolute; top: 28px; height: 22px;
    font-family: "Playfair Display", serif; font-weight: 700; font-size: 17px;
    color: var(--paper); line-height: 22px; padding: 0 6px;
  }
  .page--left .section-tag { left: 24px; width: 548px; background: var(--sun-yellow); }
  .page--right .section-tag { left: 28px; width: 548px; background: var(--tag-red); text-align: right; }

  .headline { position: absolute; font-family: "Playfair Display", serif; font-weight: 700; }
  .headline--sun { left: 30px; top: 130px; font-size: 50px; line-height: 60px; color: var(--sun-yellow); letter-spacing: -0.3px; }
  .headline--light { left: 27px; top: 124px; font-size: 96px; line-height: 100px; color: var(--leaf-green); letter-spacing: -0.5px; }

  .standfirst { position: absolute; font-family: "Jost", sans-serif; font-style: italic; }
  .standfirst--sun { left: 336px; top: 211px; font-size: 24px; color: var(--paper); }
  .standfirst--light { left: 395px; top: 237px; font-size: 24px; line-height: 28px; color: var(--ink-soft); }

  .column {
    position: absolute; width: 170px;
    font-family: "Jost", sans-serif; font-size: 12.6px; line-height: 16.2px;
    text-align: justify; hyphens: manual;
  }
  .page--left .column { color: var(--ink); top: 262px; }
  .page--right .column { color: var(--ink-soft); top: 362px; }
  .column h3 {
    font-family: "Playfair Display", serif; font-weight: 700; font-size: 17px;
    line-height: 20px; margin: 8px 0 2px; text-align: left;
  }
  .page--left .column h3 { color: var(--paper); }
  .page--right .column h3 { color: var(--leaf-green); }
  .dropcap {
    float: left; font-size: 74px; line-height: 60px; margin: 2px 4px 0 0;
    font-family: "Jost", sans-serif; font-weight: 300;
  }
  .page--left .dropcap { color: var(--paper); }
  .page--right .dropcap { color: var(--ink-soft); }
  .spaced { letter-spacing: 3px; }

  .info-box {
    position: absolute; left: 213px; top: 636px; width: 245px; height: 100px;
    background: var(--box-green); border-radius: 10px; padding: 10px 10px;
    color: var(--paper);
  }
  .info-box h4 { font-family: "Playfair Display", serif; font-weight: 700; font-size: 18px; margin-bottom: 6px; }
  .info-box p { font-family: "Jost", sans-serif; font-style: italic; font-size: 12.6px; line-height: 17px; }

  .folio {
    position: absolute; top: 742px; font-family: "Playfair Display", serif;
    font-weight: 700; font-size: 13px;
  }
  .page--left .folio { color: var(--sun-yellow); }
  .page--right .folio { color: var(--ink-soft); }
  .folio--num { font-size: 14px; }
  .page--right .masthead-mark { color: var(--leaf-green); }
</style>
</head>
<body>
<div class="spread">

  <section class="page page--left">
    <div class="photo-solar" role="img" aria-label="Photograph of a solar panel field under a bright sun in a blue sky"></div>
    <div class="section-tag">Advertorial</div>
    <h1 class="headline headline--sun">Powered by<br>the sunlight</h1>
    <p class="standfirst standfirst--sun">We read it, we share.</p>

    <div class="column" style="left:30px">
      <p><span class="dropcap">S</span>o hi, obus sesid confex sena nonstum nonsul&shy;torio, taliciam, quium incepes&shy;Non tem ver&shy;issu libusa re muscem iumus, et;To elicaet? Risquam tereis. Cessenam sa vernis verbis ac movirtil huideni hiBi incemus num estrionsunt, que arbi fit. Tor untiu voc mius et ven&shy;tus, ficte, que prox manteret iliamquit; ne forteli, nos&shy;traedees vis, utus for adela manum adhum iam nostreb</p>
    </div>
    <div class="column" style="left:217px">
      <p>efaceris, ut verfex nos vi&shy;conum nonsulegili iaequam sens se, estrice lissidi pra ves&shy;tracta vastis. Valabulvili, Cat.</p>
      <h3>The basics</h3>
      <p>Si iaequa reviliculus cris. Ad mum cae clego avo, morte, Paliamed con andientiliam usquonf ecurorae ne confina tustre, te non hos in peris dem dum tuam nicultus, cae nosta vividelatrum con vero cae iam perce eorteris. Graet ia</p>
    </div>
    <div class="column" style="left:404px">
      <p>deffrem arei im noximussa rescrum porum consusq ua&shy;mendit quod nostemus. Axi&shy;mus liissi fachucta, lint iliciam poXimedii considiu consis&shy;sastide liconsula duconihi&shy;cam hus</p>
      <h3>The meanings</h3>
      <p>publiae convere contere sse&shy;do, cone alestia noca adero&shy;bus in ac mo aude ad co ut finam publis. Do, quit? quon&shy;tina, consus pra milii senirium</p>
    </div>

    <span class="folio folio--num" style="left:28px">12</span>
    <span class="folio masthead-mark" style="left:460px">Tidewell Horizon</span>
  </section>

  <section class="page page--right">
    <div class="photo-bulb" role="img" aria-label="Illustration of a white spiral energy-saving bulb shaped like a flower on a green stem"></div>
    <div class="section-tag">Innovations</div>
    <h2 class="headline headline--light">Let there<br>be light</h2>
    <p class="standfirst standfirst--light">What are LEDs<br>and how should<br>we use them.</p>

    <div class="column" style="left:28px">
      <p><span class="dropcap">K</span>o hi, obus sesid confex sena nonstum nonsul&shy;torio, taliciam, quium incepes&shy;Non tem ver&shy;issu libusa re muscem iumus, et;To elicaet? Risquam tereis. Cessenam sa vernis verbis ac movirtil huideni hiBi incemus adducercem, nonverri pata&shy;manum adhum iam nostreb efaceris, ut verfex nos crissus ceme di pris. Robut acchuid erfirib utebatiam sens se, trarter estrice lissidi pra ves&shy;tracta vastis. Valabulvili, Cat.</p>
      <h3>What do they do?</h3>
      <p>Si iaequa reviliculus cris. Ad mum cae clego avo, morte, Paliamed con andientiliam usquonf ecurorae ne confina tustre, te non hos in peris dem dum tuam nicultus, cae nosta</p>
    </div>
    <div class="column" style="left:215px">
      <p>vividelatrum con vero cae iam utus for adela manum adhum iam nostreb efac&shy;eris, ut convere verfex nos viconum manum<br><span class="spaced">nonsulecam</span><br>manum adhum<br>convere lissidi<br>su convere convere convere.</p>
      <h3>The conclusion</h3>
      <p>publiae convere contere sse&shy;do, cone alestia noca adero&shy;bus in ac mo aude ad co ut tina, consus pra milii manum adhum iam nostreb sum.</p>
    </div>

    <aside class="info-box">
      <h4>More about the LEDs</h4>
      <p>De es, fordiem overic tus, que aperess erimus iam nonsula vit, con inatum inatilles vius nortum ad des habem se .</p>
    </aside>

    <span class="folio masthead-mark" style="left:28px">Tidewell Horizon</span>
    <span class="folio folio--num" style="left:548px">13</span>
  </section>

</div>
</body>
</html>
```